Marrowby Water Taxi and Transport Business Card

I need business cards for my new water taxi and freight transport business I have started here in Kodiak Alaska. Kodiak is a remote island in the middle of the gulf of Alaska. There are seven native villages around the island and Kodiak is the #2 fishing port in the United States. We also have the largest Coast Guard Base in the U.S. My company will be providing water taxi and freight transport logistics to the villages and many hunting and fishing lodges as well as remote properties around the island.

I would like a business card that isn't status quo, something that stands out, either in feel or appearance. I do like clean minimal designs but it needs to have the necessary contact info on it.

Target Market(s)

remote lodge / property owners, residents of the many villages around Kodiak and any one wanting to enjoy the great outdoors of Kodiak Alaska

Industry/Entity Type

Business

Contact Information for Business Card

I like clean simple designs that aren't cluttered but still provide the necessary information

Colors
0255a3
3277b5
33a4d5
9bcb3c
add136
fbed22
ffc214
f78f20
f37122

Requirements
Must have
• logo and contact info
• Captain Mason Elwick
• www.marrowbyferryline.com
• mason@marrowbyferryline.com

```html
<!DOCTYPE html>
<html lang="en">
<head>
<meta charset="utf-8">
<title>Marrowby Water Taxi &amp; Transport – Business Card</title>
<link rel="stylesheet" href="https://fonts.googleapis.com/css2?family=Open+Sans:wght@400;600;700&display=swap">
<style>
  :root {
    --navy: #1157a7;
    --sky: #23a9e1;
    --paper: #ffffff;
    --backdrop: #e9e7e4;
    --ink-white: #ffffff;
  }
  * { margin: 0; padding: 0; box-sizing: border-box; }
  html, body { width: 1200px; height: 900px; overflow: hidden; }
  body {
    position: relative;
    background: var(--backdrop);
    font-family: "Open Sans", Arial, sans-serif;
  }
  .card {
    position: absolute;
    background: var(--paper);
    overflow: hidden;
    box-shadow: 0 2px 8px rgba(0,0,0,0.12);
  }
  .card--front { left: 78px; top: 34px; width: 588px; height: 364px; }
  .card--back  { left: 388px; top: 505px; width: 567px; height: 352px; }

  .brand {
    position: absolute;
    left: 0; right: 0;
    text-align: center;
    color: var(--navy);
    font-weight: 600;
    line-height: 1;
  }
  .brand__name { display: block; font-size: 60px; letter-spacing: 1px; }
  .brand__tagline { display: block; font-size: 25px; margin-top: 6px; }
  .card--front .brand { top: 52px; }
  .card--back .brand { top: 180px; }
  .card--back .brand__name { font-size: 58px; }
  .card--back .brand__tagline { font-size: 24px; }

  .band { position: absolute; left: 0; top: 0; width: 588px; height: 364px; }

  .contact {
    position: absolute;
    left: 0; right: 0; top: 244px;
    text-align: center;
    color: var(--ink-white);
  }
  .contact__name { font-size: 21px; font-weight: 700; margin-bottom: 14px; }
  .contact__line {
    display: flex; align-items: center; justify-content: center;
    gap: 8px; font-size: 15px; line-height: 25px;
  }
  .contact__icon { width: 12px; height: 12px; }
</style>
</head>
<body>

  <section class="card card--front" aria-label="Business card front">
    <svg class="band" viewBox="0 0 588 364" aria-hidden="true">
      <polygon points="0,199 398,199 373,224 0,224" fill="var(--sky)"/>
      <polygon points="0,228 377,228 415,190 588,190 588,364 0,364" fill="var(--navy)"/>
    </svg>

    <div class="brand">
      <span class="brand__name">MARROWBY</span>
      <span class="brand__tagline">Water Taxi &amp; Transport</span>
    </div>

    <div class="contact">
      <p class="contact__name">Captain Mason Elwick</p>
      <p class="contact__line">
        <svg class="contact__icon" viewBox="0 0 12 12" aria-hidden="true">
          <rect x="0.5" y="2" width="11" height="8" fill="#fff"/>
          <polyline points="0.5,2 6,6.5 11.5,2" fill="none" stroke="#1157a7" stroke-width="1.2"/>
        </svg>
        mason@marrowbyferryline.com
      </p>
      <p class="contact__line">
        <svg class="contact__icon" viewBox="0 0 12 12" aria-hidden="true">
          <g fill="none" stroke="#fff" stroke-width="1.6" stroke-linecap="round">
            <path d="M5 7 L7 5"/>
            <path d="M4.5 5.5 L2.8 7.2 a1.8 1.8 0 0 0 2.5 2.5 L7 8"/>
            <path d="M7.5 6.5 L9.2 4.8 a1.8 1.8 0 0 0 -2.5 -2.5 L5 4"/>
          </g>
        </svg>
        www.marrowbyferryline.com
      </p>
    </div>
  </section>

  <section class="card card--back" aria-label="Business card back">
    <div class="brand">
      <span class="brand__name">MARROWBY</span>
      <span class="brand__tagline">Water Taxi &amp; Transport</span>
    </div>
  </section>

</body>
</html>
```